Coach Bruno Velasque Life Coach webpage

I am a Triathlon Coach but now I am in the process of opening a "new brand" as a Life Coach therefore I need new image and a new webpage. I live in Mexico city and would like to offer my services to Latinamerican clientes (spanish speaking). My actual website is www.trenquo.mx. My new website should help me to communicate what I do (Life Coaching), how my services are different from others, help gain new clients through one on one sessions, and I also offer a mental training course. I would like to see designs from a ZEN perspective (minimalistic, light and peaceful colors and not strong colors like my current webpage). The final design should communicate a sense of peace, tranquility, accomplishment and accompaniment. I would like to be able to manipulate the information and add-ons such a section were people can buy, subscribe and pay for the courses.

Target Market(s)

Male and female between 35 and 60 years who are going through changes in their life, need to make important decisions (such a divorcing or not, quitting or changing jobs, or not, etc), and or who do not fell happy with their current life.

Industry/Entity Type

Coaching

Coding

Coded - Design and coding required

Number of Pages Required

5+ page

Font styles to use
Sans Serif

Colors

Designer to choose colors to be used in the design.

Requirements
Must have
• 6 sections and one of those sections a place where my clients can buy courses and pay for them there. I would like to be able to change some of the information easily. I would like to see designs from a ZEN perspective (minimalistic, light and peaceful colors and not strong colors like my current webpage). The final design should communicate a sense of peace, tranquility, accomplishment and accompaniment. I would like to be able to manipulate the informati
Should not have
• dark strong colors

```html
<!DOCTYPE html>
<html lang="en">
<head>
<meta charset="utf-8">
<title>Bruno Velasque · Life Coach</title>
<link href="https://fonts.googleapis.com/css2?family=Josefin+Sans:wght@400;600;700&family=Lato:wght@400;700&display=swap" rel="stylesheet">
<style>
:root{
  --accent:#d58c6f;
  --accent-bg:#dc9d85;
  --sage:#bcd8d2;
  --sage-btn:#9cc3bb;
  --ink:#1f1f1f;
  --muted:#555;
  --white:#fff;
  --foot:#e8e6e6;
  --field:#ececec;
}
*{box-sizing:border-box;margin:0;padding:0}
html,body{width:1200px;height:5338px;overflow:hidden}
body{font-family:'Lato',sans-serif;color:var(--ink);background:var(--white);position:relative}
.head{font-family:'Josefin Sans',sans-serif}
section,header,footer{position:absolute;left:0;width:1200px}
.abs{position:absolute}
.btn{position:absolute;font-family:'Josefin Sans',sans-serif;font-weight:600;font-size:14px;display:flex;align-items:center;justify-content:center;border-radius:4px}
.btn-accent{background:var(--accent);color:var(--white)}
.btn-sage{background:var(--sage-btn);color:var(--ink)}
.swoosh{position:absolute;width:64px;height:18px}
.photo{position:absolute}
/* nav */
.topbar{top:0;height:52px;border-top:4px solid var(--accent);background:var(--white)}
.logo{position:absolute;left:110px;top:8px;font-family:'Josefin Sans',sans-serif;font-size:32px}
.nav a{position:absolute;top:20px;font-size:13px;color:var(--ink);text-decoration:none}
.nav a.on{color:var(--accent)}
/* hero */
.hero{top:52px;height:595px;background:linear-gradient(100deg,#5c4a3e 0%,#8a7563 35%,#e5e1da 60%,#cfc7bd 100%)}
.hero .welcome{left:118px;top:200px;color:#fff;font-size:32px;letter-spacing:2px}
.hero .name{left:108px;top:240px;color:#fff;font-size:72px;font-weight:700;letter-spacing:2px}
/* about */
.about{top:700px;height:540px}
.about .photo{left:170px;top:32px;width:340px;height:441px;border-radius:150px 0 0 0;background:linear-gradient(160deg,#c9d3d6,#7b5a45 60%,#3e3430)}
.about h2{left:642px;top:52px;font-size:44px;font-weight:400}
.about h2 span{color:var(--accent)}
.about .copy{left:642px;top:108px;width:450px;font-size:11.5px;line-height:26px;color:var(--muted)}
.about .copy p{margin-bottom:8px}
/* benefits */
.benefits{top:1258px;height:572px;background:var(--sage)}
.sec-title{position:absolute;width:100%;text-align:center;font-family:'Josefin Sans',sans-serif;font-size:42px}
.sec-title span{color:var(--accent)}
.benefit{position:absolute;top:180px;width:300px;text-align:center}
.ring{width:124px;height:124px;border-radius:50%;border:4px solid #fff;margin:0 auto;display:flex;align-items:center;justify-content:center;background:#fff}
.ring.hot{background:var(--accent);border:3px dashed #fff}
.benefit p{margin-top:26px;font-size:12px;line-height:28px;color:var(--ink)}
/* services */
.services{top:1830px;height:655px}
.svc{position:absolute;top:180px;width:475px;height:386px;background:#fff;border-radius:0 0 28px 0;box-shadow:0 4px 14px rgba(0,0,0,.12)}
.svc .photo{left:0;top:0;width:475px;height:326px;border-radius:22px 0 28px 0}
.svc h3{position:absolute;bottom:18px;width:100%;text-align:center;font-family:'Josefin Sans',sans-serif;font-weight:400;font-size:20px;letter-spacing:1px}
/* products */
.products{top:2485px;height:582px;background:var(--accent-bg)}
.products h2{position:absolute;left:112px;top:52px;font-size:42px;color:#fff;font-weight:400;font-family:'Josefin Sans',sans-serif}
.arrow{position:absolute;top:78px;width:26px;height:26px;border-radius:50%;background:#fff;display:flex;align-items:center;justify-content:center}
.arrow.dim{opacity:.45}
.prod{position:absolute;top:143px;width:313px;height:375px;background:#fff;border-radius:4px}
.prod .photo{left:40px;top:40px;width:233px;height:190px;border-radius:6px}
.prod .pname{position:absolute;left:28px;top:282px;font-family:'Josefin Sans',sans-serif;font-size:20px}
.prod .price{position:absolute;right:24px;top:282px;font-size:19px}
.prod .btn{left:28px;top:321px;width:114px;height:30px}
/* blog */
.blog{top:3067px;height:680px}
.post{position:absolute;top:187px;width:313px;height:373px;background:#fff;box-shadow:0 2px 10px rgba(0,0,0,.1)}
.post .photo{left:0;top:0;width:313px;height:209px}
.post .tag{position:absolute;left:14px;top:228px;font-size:13px;color:var(--accent)}
.post h4{position:absolute;left:14px;top:252px;width:290px;font-weight:400;font-size:16px;line-height:26px}
.post .meta{position:absolute;left:14px;top:327px;font-size:11px;color:#777;display:flex;gap:24px}
/* faq */
.faq{top:3747px;height:527px;background:var(--sage)}
.faq h2{position:absolute;left:110px;top:50px;font-size:42px;font-weight:400;font-family:'Josefin Sans',sans-serif}
.q{position:absolute;left:112px;width:489px;height:56px;background:#fff;border-radius:3px;font-size:11.5px;display:flex;align-items:center;justify-content:space-between;padding:0 26px}
.q.open{background:var(--accent);color:#fff}
.answer{position:absolute;left:642px;top:143px;width:446px;height:299px;background:#fff;padding:34px 38px}
.answer h5{font-size:17px;font-weight:400;line-height:28px;margin-bottom:28px}
.answer p{font-size:11.5px;line-height:28px;color:var(--muted)}
/* contact */
.contact{top:4274px;height:609px}
.contact h2{position:absolute;left:112px;top:86px;font-size:42px;font-weight:400;font-family:'Josefin Sans',sans-serif}
.contact h2 span{color:var(--accent)}
.field{position:absolute;left:112px;width:530px;height:62px;background:var(--field);border-radius:3px;display:flex;align-items:center;padding-left:18px;gap:12px;font-size:12px;color:#666}
.contact .photo{left:736px;top:91px;width:352px;height:435px;border-radius:150px 0 0 0;background:linear-gradient(150deg,#e9e5de,#6b5a52 55%,#2e2a2a)}
/* footer */
.foot{top:4883px;height:455px;background:var(--foot)}
.foot .flogo{position:absolute;left:114px;top:50px;font-family:'Josefin Sans',sans-serif;font-size:54px}
.sub{position:absolute;left:555px;top:58px;width:531px;height:54px;background:#fff;border-radius:4px;font-size:12px;color:#666;display:flex;align-items:center;padding-left:20px}
.sub .btn{left:425px;top:0;width:106px;height:54px;border-radius:0 4px 4px 0}
.col{position:absolute;top:175px}
.col h6{font-size:19px;font-weight:400;text-decoration:underline;margin-bottom:20px}
.col li{list-style:none;font-size:13px;line-height:29px}
.ci{display:flex;align-items:center;gap:14px;font-size:13px;height:47px;white-space:nowrap}
.ci i{width:24px;height:24px;background:#cfcfcf;border-radius:4px;display:flex;align-items:center;justify-content:center}
.soc{display:flex;align-items:center;gap:12px;font-size:13px;height:44px}
.soc i{width:20px;height:20px;border-radius:3px;background:#cfcfcf}
.soc.hot i{background:var(--accent)}
.soc.hot span{color:var(--accent);text-decoration:underline}
.rule{position:absolute;left:110px;top:421px;width:978px;height:1px;background:#999}
.copy-r{position:absolute;top:433px;width:100%;text-align:center;font-size:12px}
</style>
</head>
<body>
<svg width="0" height="0" style="position:absolute">
  <defs>
    <symbol id="sw" viewBox="0 0 64 18"><path d="M6 14 C18 6 30 6 34 9 C38 12 46 10 58 4" fill="none" stroke="#1f1f1f" stroke-width="3" stroke-linecap="round"/><path d="M14 9 L40 8" stroke="#1f1f1f" stroke-width="2" stroke-linecap="round"/></symbol>
    <symbol id="swW" viewBox="0 0 64 18"><path d="M6 14 C18 6 30 6 34 9 C38 12 46 10 58 4" fill="none" stroke="#fff" stroke-width="3" stroke-linecap="round"/><path d="M14 9 L40 8" stroke="#fff" stroke-width="2" stroke-linecap="round"/></symbol>
    <symbol id="chev" viewBox="0 0 16 16"><path d="M3 6 L8 11 L13 6" fill="none" stroke="#1f1f1f" stroke-width="2"/></symbol>
  </defs>
</svg>

<header class="topbar">
  <div class="logo">Bruno Velasque</div>
  <nav class="nav">
    <a class="on" style="left:398px">Start</a>
    <a style="left:476px">About Me</a>
    <a style="left:584px">Services</a>
    <a style="left:679px">Blog</a>
    <a style="left:753px">FAQ's</a>
  </nav>
  <div class="btn btn-accent" style="left:1003px;top:8px;width:85px;height:32px;font-weight:400">Contact</div>
</header>

<section class="hero">
  <div class="photo" role="img" aria-label="Coach in a bright lounge talking with a client seated on a white sofa" style="inset:0"></div>
  <div class="abs head welcome">Welcome To</div>
  <div class="abs head name">Bruno Velasque</div>
  <div class="btn btn-accent" style="left:112px;top:344px;width:298px;height:31px">Schedule a Free Consultation Session</div>
</section>

<section class="about">
  <div class="photo" role="img" aria-label="Portrait of the coach holding a notebook by a window"></div>
  <h2 class="abs head">About <span>Me</span></h2>
  <svg class="swoosh" style="left:642px;top:96px"><use href="#sw"/></svg>
  <div class="abs copy">
    <p>I am Bruno Velasque, coach of life and sport with more than 20 years of experience as an athlete of high performance and trainer of champions. My mission is to guide you to find a balance between body, mind and spirit, so that you can achieve your goals in a full and balanced way.</p>
    <p>A través de un enfoque integral que combina el trainamento físico y mental, I accompany you to discover your maximum potential and to live a life in harmony with your dreams and values.</p>
    <p>Aquí, te invito a surpar tus límites y a descubrí de lo que realente eres capaz. With personalized programs, courses of mental training and un compromiso genuino por tu bienestar, juntos lograremos que te conviertas en tu mejor versión.</p>
  </div>
  <div class="btn btn-sage" style="left:642px;top:425px;width:113px;height:32px">Read More</div>
</section>

<section class="benefits">
  <div class="sec-title" style="top:76px">Benefits of Life Coaching</div>
  <svg class="swoosh" style="left:570px;top:122px"><use href="#sw"/></svg>
  <div class="benefit" style="left:107px">
    <div class="ring"><svg width="60" height="60" viewBox="0 0 60 60" fill="none" stroke="#d58c6f" stroke-width="2"><circle cx="32" cy="20" r="9"/><path d="M29 30h6M30 34h4M32 5v3M20 10l2 2M44 10l-2 2M8 44h10l8 4h12l10-8M8 52h14l10 2"/></svg></div>
    <p>Life coaching offers you the opportunity to rediscover yourself and define the path to your goals with clarity and purpose.</p>
  </div>
  <div class="benefit" style="left:445px">
    <div class="ring hot"><svg width="60" height="60" viewBox="0 0 60 60" fill="none" stroke="#fff" stroke-width="2"><circle cx="34" cy="22" r="10"/><circle cx="34" cy="22" r="4"/><path d="M8 44h10l8 4h12l10-8M8 52h14l10 2"/></svg></div>
    <p>Personalized support, coaching helps you identify and overcome the obstacles that hold you back, whether they are fears, insecurities or lack of direction.</p>
  </div>
  <div class="benefit" style="left:778px">
    <div class="ring"><svg width="60" height="60" viewBox="0 0 60 60" fill="none" stroke="#d58c6f" stroke-width="2"><path d="M22 52V40c-6-4-8-10-6-17 3-10 16-13 24-7 6 5 6 12 3 17l3 6h-4v7h-8v6"/><circle cx="30" cy="26" r="6"/></svg></div>
    <p>life coaching you develop a positive and proactive mindset that allows you to face challenges with confidence and focus.</p>
  </div>
</section>

<section class="services">
  <div class="sec-title" style="top:84px">Our <span>Services</span></div>
  <svg class="swoosh" style="left:568px;top:128px"><use href="#sw"/></svg>
  <div class="svc" style="left:112px">
    <div class="photo" role="img" aria-label="Coach in conversation with a client in a bright room" style="background:linear-gradient(135deg,#e9e3da,#b58464 55%,#d9cfc3)"></div>
    <h3>Personalized life coaching</h3>
  </div>
  <div class="svc" style="left:611px">
    <div class="photo" role="img" aria-label="Group of people seated in a circle during a training session" style="background:linear-gradient(135deg,#d9dcdc,#8c8a82 50%,#e3e0da)"></div>
    <h3>Mental Training Courses</h3>
  </div>
</section>

<section class="products">
  <h2>Our Products</h2>
  <svg class="swoosh" style="left:112px;top:100px"><use href="#swW"/></svg>
  <div class="arrow" style="left:1025px"><svg width="12" height="12" viewBox="0 0 12 12"><path d="M8 2L4 6l4 4" fill="none" stroke="#d58c6f" stroke-width="2"/></svg></div>
  <div class="arrow dim" style="left:1058px"><svg width="12" height="12" viewBox="0 0 12 12"><path d="M4 2l4 4-4 4" fill="none" stroke="#d58c6f" stroke-width="2"/></svg></div>
  <div class="prod" style="left:112px">
    <div class="photo" role="img" aria-label="Stack of books" style="background:linear-gradient(180deg,#f4f1ee,#b96e4a 50%,#5d7da6)"></div>
    <div class="pname">E-Books</div><div class="price">$43.00</div>
    <div class="btn btn-sage">Add To Cart</div>
  </div>
  <div class="prod" style="left:443px">
    <div class="photo" role="img" aria-label="Essential oil bottles with a diffuser and candle" style="background:linear-gradient(180deg,#f6f4f0,#c9a27e 50%,#6e4a2e)"></div>
    <div class="pname">Wellness Products</div><div class="price">$43.00</div>
    <div class="btn btn-sage">Add To Cart</div>
  </div>
  <div class="prod" style="left:773px">
    <div class="photo" role="img" aria-label="Illustration of an online training screen" style="background:linear-gradient(180deg,#f6f7f9,#c9d5e6 50%,#e59a6b)"></div>
    <div class="pname">Training</div><div class="price">$43.00</div>
    <div class="btn btn-sage">Add To Cart</div>
  </div>
</section>

<section class="blog">
  <div class="sec-title" style="top:86px">Our <span>Blog</span></div>
  <svg class="swoosh" style="left:568px;top:130px"><use href="#sw"/></svg>
  <div class="post" style="left:112px">
    <div class="photo" role="img" aria-label="Two women reviewing notes together" style="background:linear-gradient(135deg,#e1e3e4,#a69586 50%,#dcdad6)"></div>
    <div class="tag">News</div>
    <h4>The Power of Positive Thinking Transform Your Mindset</h4>
    <div class="meta"><span>▦ Oct 29,2024</span><span>▭ 4 Comments</span></div>
  </div>
  <div class="post" style="left:443px">
    <div class="photo" role="img" aria-label="Two women talking at a table" style="background:linear-gradient(135deg,#ddd8d0,#9b8b7a 50%,#e6e4e0)"></div>
    <div class="tag">News</div>
    <h4>Mindfulness Techniques for Everyday Life</h4>
    <div class="meta"><span>▦ Oct 30,2024</span><span>▭ 4 Comments</span></div>
  </div>
  <div class="post" style="left:773px">
    <div class="photo" role="img" aria-label="Hiker with raised arms facing a misty landscape" style="background:linear-gradient(180deg,#dfe6e8,#b9c4c6 60%,#8e8a7f)"></div>
    <div class="tag">News</div>
    <h4>Setting Achievable Goals: The SMART Method Explained</h4>
    <div class="meta"><span>▦ Oct 31,2024</span><span>▭ 4 Comments</span></div>
  </div>
  <div class="btn btn-sage" style="left:557px;top:564px;width:88px;height:31px">View All</div>
</section>

<section class="faq">
  <h2>Frequently Asked Questions?</h2>
  <svg class="swoosh" style="left:112px;top:96px"><use href="#sw"/></svg>
  <div class="q" style="top:141px">1.What are the benefits of life coaching?<svg width="16" height="16"><use href="#chev"/></svg></div>
  <div class="q" style="top:203px">2.How many sessions do I need to see results?<svg width="16" height="16"><use href="#chev"/></svg></div>
  <div class="q open" style="top:267px">3.What is a life and sports coach, and how can they help me?<svg width="16" height="16" viewBox="0 0 16 16"><path d="M6 3l5 5-5 5" fill="none" stroke="#fff" stroke-width="2"/></svg></div>
  <div class="q" style="top:330px">4.How are these programs different from other workouts?<svg width="16" height="16"><use href="#chev"/></svg></div>
  <div class="q" style="top:394px">5.How can I start working with you?<svg width="16" height="16"><use href="#chev"/></svg></div>
  <div class="answer">
    <h5>3.What is a life and sports coach, and how can they help me?</h5>
    <p>Un coach de vida y deportivo te guía en el logro de tus metas personales y deportivas, trabajando tanto en tu bienestar físico como mental. Te ayuda a mejorar tu rendimiento, a mantener un equilibrio saludable y a superar obstáculos para alcanzar una vida más plena y satisfactoria.</p>
  </div>
</section>

<section class="contact">
  <h2>Get In Touch <span>With Us</span></h2>
  <svg class="swoosh" style="left:112px;top:130px"><use href="#sw"/></svg>
  <div class="field" style="top:165px">👤 Name</div>
  <div class="field" style="top:238px">✉ Email</div>
  <div class="field" style="top:310px">☏ Phone</div>
  <div class="field" style="top:383px">▤ Message</div>
  <div class="btn btn-sage" style="left:112px;top:466px;width:114px;height:31px">Submit Now</div>
  <div class="photo" role="img" aria-label="Two businesswomen laughing together in an office"></div>
</section>

<footer class="foot">
  <div class="flogo">Bruno Velasque</div>
  <div class="sub">Enter Email Address<div class="btn btn-accent">Subscribe</div></div>
  <div class="col" style="left:110px"><h6>Quick Links</h6><ul><li>Start</li><li>About Me</li><li>Services</li><li>Blog</li><li>Contact</li><li>FAQ's</li></ul></div>
  <div class="col" style="left:363px"><h6>Other Links</h6><ul><li>Privacy Policy</li><li>Terms &amp; Conditions</li><li>Disclaimer</li><li>Support</li><li>Help</li></ul></div>
  <div class="col" style="left:632px"><h6>Contact Info</h6>
    <div class="ci"><i><svg width="12" height="14" viewBox="0 0 12 14"><path d="M6 13C2 8 1 6 1 5a5 5 0 0110 0c0 1-1 3-5 8z" fill="#fff"/></svg></i>Calle Olmo 24, CDMX -06700</div>
    <div class="ci"><i><svg width="14" height="14" viewBox="0 0 14 14"><path d="M3 1l3 3-2 2c1 2 2 3 4 4l2-2 3 3-2 2C6 13 1 8 1 3z" fill="#fff"/></svg></i>+52 55 4821 3307</div>
    <div class="ci"><i><svg width="14" height="12" viewBox="0 0 14 12"><rect x="1" y="2" width="12" height="8" fill="none" stroke="#fff" stroke-width="1.5"/><path d="M1 2l6 5 6-5" fill="none" stroke="#fff" stroke-width="1.5"/></svg></i>hola@brunovelasque.mx</div>
  </div>
  <div class="col" style="left:972px"><h6>Follow US</h6>
    <div class="soc hot"><i></i><span>Socialbook</span></div>
    <div class="soc"><i></i><span>Snapgram</span></div>
    <div class="soc"><i></i><span>Workednet</span></div>
  </div>
  <div class="rule"></div>
  <div class="copy-r">© 2024 &nbsp;Bruno Velasque. All rights reserved.</div>
</footer>
</body>
</html>
```